New Business Card for chocolate Company

I am looking to have business cards for my Chocolate Company Velvet Bramble Sweets.
I hand make all organic, fair trade, vegan, gluten free, allergy friendly chocolate. We are located in Austin Texas and are very Proud to be a locally made good. I have my logo and new sticker design for our boxes but now I need cards. I was thinking either natural craft or white. But I want to have a bit of funk to the cards so someone will hold onto it for a long time.
The important info is
Dana Pirrowe
Owner and Chocolatier
Velvet Bramble Sweets
velvetbramblesweetsfx.com
velvetbramblesweets@mailvora.com
velvetbramblesweets on instagram
512.306.4178

Velvet Bramble sweets are Vegan ,Gluten free, organic, fair trade, allergy friendly hand made chocolate.

Target Market(s)

We cater to all ages. Our chocolate is on the higher price scale and is a decadent treat. But we make custom molds for any event kids party's to an elegant wedding.

Industry/Entity Type

Business

Requirements
Must have
• Good design logo and some sort of austin vibe.

```html
<!DOCTYPE html>
<html lang="en">
<head>
<meta charset="utf-8">
<title>Velvet Bramble Sweets — Business Card</title>
<link rel="stylesheet" href="https://fonts.googleapis.com/css2?family=Michroma&family=Quicksand:wght@400&display=swap">
<style>
  :root {
    --backdrop: #6d6966;
    --card-paper: #f5f4f1;
    --gold: #8e7a45;
    --gold-tint: #ddd4bd;
    --ink: #3a3a3a;
    --ink-soft: #555555;
  }
  * { margin: 0; padding: 0; box-sizing: border-box; }
  html, body {
    width: 1035px;
    height: 1200px;
    overflow: hidden;
    background: var(--backdrop);
  }
  .canvas {
    position: relative;
    width: 1035px;
    height: 1200px;
  }
  .card {
    position: absolute;
    top: 320px;
    width: 340px;
    height: 560px;
    background: var(--card-paper);
  }
  .card--back { left: 120px; }
  .card--front { left: 575px; }

  .divider-area {
    position: absolute;
    left: 31px;
    width: 278px;
    height: 12px;
    background: linear-gradient(90deg, var(--card-paper), var(--gold-tint) 50%, var(--card-paper));
  }
  .divider-area--top { top: 86px; }
  .divider-area--bottom { top: 452px; }

  .contact-block {
    position: absolute;
    left: 0;
    width: 100%;
    text-align: center;
  }
  .owner-name {
    top: 158px;
    font-family: "Michroma", sans-serif;
    font-size: 14px;
    font-weight: 400;
    letter-spacing: 2.5px;
    color: var(--ink);
  }
  .owner-title {
    top: 194px;
    font-family: "Michroma", sans-serif;
    font-size: 10.5px;
    letter-spacing: 2px;
    color: var(--gold);
  }
  .contact-list {
    top: 266px;
    list-style: none;
    font-family: "Quicksand", sans-serif;
    font-size: 12.5px;
    letter-spacing: 1.2px;
    line-height: 28.5px;
    color: var(--ink-soft);
  }

  .wordmark {
    position: absolute;
    top: 50%;
    left: 0;
    width: 100%;
    transform: translateY(-50%);
    text-align: center;
    font-family: "Michroma", sans-serif;
    font-size: 31px;
    line-height: 1.5;
    letter-spacing: 1px;
    color: var(--gold);
  }
  .wordmark span { display: block; }
</style>
</head>
<body>
<main class="canvas">

  <section class="card card--back" aria-label="Contact side">
    <div class="divider-area divider-area--top" role="img" aria-label="Decorative rule with a small centred ornament"></div>

    <h1 class="contact-block owner-name">DANA PIRROWE</h1>
    <p class="contact-block owner-title">OWNER AND CHOCOLATIER</p>

    <ul class="contact-block contact-list">
      <li>Velvet Bramble Sweets</li>
      <li>512.306.4178</li>
      <li>velvetbramblesweets@mailvora.com</li>
      <li>velvetbramblesweets on instagram</li>
      <li>velvetbramblesweetsfx.com</li>
    </ul>

    <div class="divider-area divider-area--bottom" role="img" aria-label="Decorative rule with a small centred ornament"></div>
  </section>

  <section class="card card--front" aria-label="Brand side">
    <p class="wordmark">
      <span>VELVET</span>
      <span>BRAMBLE</span>
      <span>SWEETS</span>
    </p>
  </section>

</main>
</body>
</html>
```